1876 Basins & Spouts Business Card

I'm wanting to get a business card designed. Our business is 1876 Basins & Spouts
Details for the card:

1876 Basins & Spouts
Name: Harold Vesk
Email: harold@1876basinsandspouts.com.au
Website: www.1876basinsandspouts.com.au
Mobile: 0438 260 947
Phone: 02 7481 3926

Font of Basins & Spouts is called Snell Roundhand. Not sue what font logo text is.

I'm thinking two sided but it doesn't have to be.

```html
<!DOCTYPE html>
<html lang="en">
<head>
<meta charset="utf-8">
<title>1876 Basins &amp; Spouts Business Card</title>
<link rel="stylesheet" href="https://fonts.googleapis.com/css2?family=Pinyon+Script&family=Open+Sans:wght@400&display=swap">
<style>
  :root {
    --stage: #e4e4e4;
    --paper: #ffffff;
    --ink: #1a1a1a;
    --rule: #bcbcbc;
    --dark-card: #2b2929;
    --light-ink: #f2f2f2;
  }
  * { margin: 0; padding: 0; box-sizing: border-box; }
  html, body { width: 1200px; height: 802px; overflow: hidden; background: var(--stage); }
  .canvas { position: relative; width: 1200px; height: 802px; }
  .card {
    position: absolute; top: 275px; width: 443px; height: 263px;
    box-shadow: 0 3px 8px rgba(0,0,0,.25);
  }
  .card--front { left: 136px; background: var(--paper); border-bottom: 5px solid var(--ink); color: var(--ink); }
  .card--back { left: 624px; background: var(--dark-card); color: var(--light-ink); }

  .brand {
    position: absolute; right: 32px; top: 72px;
    font-family: "Open Sans", sans-serif; font-size: 21px; line-height: 1;
    color: var(--ink); white-space: nowrap;
  }
  .tagline {
    position: absolute; right: 32px; top: 103px;
    font-family: "Open Sans", sans-serif; font-size: 7.5px; color: var(--ink); white-space: nowrap;
  }
  .holder {
    position: absolute; left: 24px; top: 158px; width: 380px;
    display: flex; align-items: center; gap: 10px;
  }
  .holder__name { font-family: "Pinyon Script", cursive; font-size: 20px; white-space: nowrap; }
  .holder__rule { flex: 1; height: 1px; background: var(--rule); margin-top: 4px; }

  .contacts {
    position: absolute; top: 204px;
    font-family: "Open Sans", sans-serif; font-size: 12px; line-height: 16px; white-space: nowrap;
  }
  .contacts--phones { left: 27px; }
  .contacts--web { right: 34px; text-align: right; }
  .contacts li { list-style: none; display: flex; align-items: center; gap: 5px; }
  .contacts--web li { justify-content: flex-end; }
  .icon { width: 9px; height: 9px; fill: var(--ink); flex: none; }

  .back-brand {
    position: absolute; left: 0; right: 0; top: 120px; text-align: center;
    font-family: "Open Sans", sans-serif; font-size: 21px; line-height: 1; color: var(--light-ink);
  }
  .back-url {
    position: absolute; left: 0; right: 0; top: 219px; text-align: center;
    font-family: "Open Sans", sans-serif; font-size: 12px; color: var(--light-ink);
  }
</style>
</head>
<body>
<div class="canvas">
  <section class="card card--front">
    <div class="brand">1876 Basins &amp; Spouts</div>
    <p class="tagline">Pairing classic elegance with durable everyday function</p>
    <div class="holder">
      <span class="holder__name">Harold Vesk</span>
      <span class="holder__rule"></span>
    </div>
    <ul class="contacts contacts--phones">
      <li><svg class="icon" viewBox="0 0 12 12"><path d="M1 4.5C1 2.5 3 1.5 6 1.5s5 1 5 3v1H8.5V4H3.5v1.5H1zM3 6h6l1.5 4.5h-9z"/></svg>0438 260 947</li>
      <li><svg class="icon" viewBox="0 0 12 12"><path d="M3 0.5h6a1 1 0 0 1 1 1v9a1 1 0 0 1-1 1H3a1 1 0 0 1-1-1v-9a1 1 0 0 1 1-1zM3.5 2v7h5V2z"/></svg>02 7481 3926</li>
    </ul>
    <ul class="contacts contacts--web">
      <li>harold@1876basinsandspouts.com.au<svg class="icon" viewBox="0 0 12 12"><path d="M0.5 2.5h11v1L6 7 0.5 3.5zM0.5 4.8 6 8.3l5.5-3.5v4.7h-11z"/></svg></li>
      <li>www.1876basinsandspouts.com.au<svg class="icon" viewBox="0 0 12 12"><circle cx="6" cy="6" r="5.5"/><path d="M3 4h3l1 2-2 2V10L3.5 7z" fill="#fff"/></svg></li>
    </ul>
  </section>

  <section class="card card--back">
    <div class="back-brand">1876 Basins &amp; Spouts</div>
    <p class="back-url">www.1876basinsandspouts.com.au</p>
  </section>
</div>
</body>
</html>
```